Psychiatric Office Needs a Website- 1st Time Ever!

Been in practice since 2003 with no website, but finally ready to dive in. We are Maplecrest Behavioral Healthcare, a mental health outpatient practice based in Fayetteville, Georgia that sees diverse individuals and families from childhood to advanced age for a variety of conditions. We've grown by word of mouth and referral but would now like to have a digital footprint. Be the pioneer of our website and we will be sure to share. We would like to see designs that are modern, animated, fairly colorful, easy to read, and caters to all ages. Also, we would like the design to take the whole page (not be centered) and can be viewed well on phone/tablet. Please see our outline for more information. Our motto/slogan is: Maplecrest Behavioral Healthcare- A step forward in your wellness journey, so the design should try to reflect that.
Updates

Project Deadline Extended
Reason: site in progress

Target Market(s)

Children through elderly

Industry/Entity Type

Medical

Logo Text

Stepping forward in your wellness journey

Number of Pages Required

1 page

Colors

Designer to choose colors to be used in the design.

Requirements
Must have
• Animation or moving pictures.
• Color.
• Concise.
• User friendly
• Diversity in the stock photos

```html
<!DOCTYPE html>
<html lang="en">
<head>
<meta charset="utf-8">
<title>Maplecrest Behavioral Healthcare</title>
<link href="https://fonts.googleapis.com/css2?family=Lato:wght@400;700&display=swap" rel="stylesheet">
<style>
:root{
  --blue:#2a90d6;
  --blue-dark:#1f7fc4;
  --green:#6db33f;
  --text:#444;
  --muted:#666;
  --line:#d9d9d9;
  --dark:#1d1d1d;
  --white:#fff;
}
*{box-sizing:border-box;margin:0;padding:0}
html,body{width:1200px;height:3352px;overflow:hidden}
body{position:relative;font-family:'Lato',sans-serif;color:var(--text);background:var(--white)}
.abs{position:absolute}
a{color:inherit;text-decoration:none}

.topbar{left:0;top:0;width:1200px;height:54px;background:var(--blue);color:var(--white);font-size:20px}
.topbar .hours{left:78px;top:14px;display:flex;align-items:center;gap:10px}
.topbar .phone{right:78px;top:14px;display:flex;align-items:center;gap:12px}

.nav{left:0;top:54px;width:1200px;height:114px;background:var(--white);box-shadow:0 3px 8px rgba(0,0,0,.15);z-index:2}
.nav a{position:absolute;top:44px;font-size:17px;color:#555}
.nav a.active{color:var(--green)}
.brand{left:508px;top:66px;width:184px;height:184px;border-radius:50%;background:var(--white);border:6px solid var(--blue);z-index:3;display:flex;align-items:center;justify-content:center;text-align:center;font-size:17px;font-weight:700;color:var(--blue);line-height:1.25;padding:20px}

.hero{left:0;top:168px;width:1200px;height:603px;background:radial-gradient(ellipse at 55% 70%,#ffe39a 0%,#f7a54a 25%,#e8683a 55%,#b8443a 80%,#6c2a2a 100%)}
.hero h1{left:78px;top:222px;width:640px;font-size:40px;font-weight:400;line-height:1.4;color:#333}
.btn{position:absolute;height:49px;border-radius:25px;background:var(--white);border:2px solid var(--blue);color:var(--blue);font-size:17px;display:flex;align-items:center;justify-content:center;letter-spacing:.5px}

.section-title{font-size:40px;font-weight:400;color:var(--text);display:flex;align-items:center;gap:24px}
.section-title .hl{color:var(--green)}
.section-title::after{content:"";flex:1;height:2px;background:var(--blue)}

.about{left:78px;top:822px;width:1044px}
.about p{margin-top:12px;width:910px;font-size:14.5px;line-height:1.75;color:var(--muted)}

.mv{left:0;top:999px;width:1200px;height:320px;background:linear-gradient(90deg,#5fae55 0%,#3f9fb8 30%,#2a8fd6 50%,#3f9fb8 70%,#5fae55 100%);color:var(--white);text-align:center}
.mv .col{top:78px;width:400px}
.mv h2{font-size:38px;font-weight:400}
.mv p{margin:10px auto 0;width:360px;font-size:13px;line-height:1.8}
.pill{display:inline-block;margin-top:16px;padding:7px 28px;border:2px solid var(--white);border-radius:20px;font-size:16px;box-shadow:inset 0 0 0 2px rgba(255,255,255,.35)}

.services{left:78px;top:1360px;width:1044px}
.brain{left:465px;top:1518px;width:270px;height:270px;border-radius:50%;background:radial-gradient(circle,#f2c34a 0%,#e45d8a 35%,#6fb6e0 65%,#f3f3f3 72%,#fff 100%)}
.ring{left:420px;top:1473px;width:360px;height:360px;border-radius:50%;border:1px solid #e6e6e6}
.svc{font-size:17px;color:var(--blue);line-height:1.3}
.svc.left{text-align:right;width:300px}
.icon{width:84px;height:84px;border-radius:50%;background:radial-gradient(circle at 40% 40%,#9ccf6a,#5a9e32);border:4px solid #eef6e6}

.conditions{left:0;top:1962px;width:1200px;height:497px;background:var(--blue)}
.conditions .section-title{position:absolute;left:78px;top:36px;width:1044px;color:var(--white)}
.conditions .section-title::after{background:rgba(255,255,255,.5);height:1px}
.cell{position:absolute;color:var(--white)}
.cell h3{font-size:24px;font-weight:400;line-height:1.15}
.cell p{font-size:14px;line-height:1.6;margin-top:6px}
.vline{position:absolute;width:1px;background:rgba(255,255,255,.35)}
.hline{position:absolute;height:1px;background:rgba(255,255,255,.35)}
.cell.boxed{border:2px solid var(--white);padding:46px 44px 0 44px}

.news{left:78px;top:2505px;width:500px}
.news .section-title::after{display:none}
.post{position:absolute;left:0;width:460px}
.post .thumb{position:absolute;left:0;top:0;width:168px;height:107px}
.post .body{position:absolute;left:174px;top:0;width:290px;font-size:14px;line-height:1.55;color:var(--muted)}
.post .body .ttl{color:var(--blue)}
.post .body .date{color:var(--blue);display:flex;align-items:center;gap:8px}
.post .body .more{color:var(--blue);font-weight:700}
.news .sep{position:absolute;left:174px;width:286px;height:1px;background:var(--line)}

.faq{left:626px;top:2505px;width:496px}
.faq .section-title{color:var(--green)}
.faq .section-title::after{display:none}
.faq-list{margin-top:18px;border:1px solid var(--line)}
.faq-item{height:45px;border-top:1px solid var(--line);display:flex;align-items:center;padding-left:12px;font-size:19px;color:var(--blue);gap:12px}
.faq-item:first-child{border-top:none;background:#f7fbfe}
.faq-item .sign{font-weight:700;font-size:22px;width:14px}
.faq-answer{height:48px;border-top:1px solid var(--line);display:flex;align-items:center;padding-left:16px;font-size:13px;color:var(--muted)}

.packet{left:0;top:2901px;width:1200px;height:139px;background:linear-gradient(90deg,#6db33f 0%,#3d9fb0 40%,#2a90d6 70%,#2a8fd6 100%);color:var(--white);font-size:42px;display:flex;align-items:center;justify-content:center}
.packet a{font-weight:700;text-decoration:underline;margin-left:12px}

.footer{left:0;top:3040px;width:1200px;height:257px;background:var(--blue-dark);color:var(--white)}
.footer h4{font-size:24px;font-weight:700}
.footer .col{position:absolute;top:24px}
.links{display:grid;grid-template-columns:170px 180px;row-gap:9px;margin-top:18px;font-size:14px}
.links span::before{content:"";display:inline-block;width:12px;height:12px;border-radius:50%;background:var(--white);margin-right:8px;vertical-align:-1px}
.tweet{display:flex;gap:12px;margin-top:18px;font-size:14px;line-height:1.45}
.tweet .dot{width:18px;height:18px;border-radius:50%;background:var(--white);flex:none;margin-top:2px}
.contact-row{display:flex;gap:14px;margin-top:16px;font-size:14px;line-height:1.45;align-items:flex-start}

.bottombar{left:0;top:3297px;width:1200px;height:55px;background:var(--dark)}
.bottombar .copy{left:78px;top:18px;font-size:14px;color:var(--green)}
.social{top:22px;width:14px;height:14px;border-radius:50%;background:var(--green)}
.totop{left:570px;top:3265px;width:60px;height:36px;background:#333;border-radius:4px 4px 0 0}
</style>
</head>
<body>

<header class="abs topbar">
  <div class="abs hours">
    <svg width="26" height="26" viewBox="0 0 26 26"><circle cx="13" cy="13" r="11" fill="none" stroke="#fff" stroke-width="2.4"/><path d="M13 6v7l5 3" fill="none" stroke="#fff" stroke-width="2.4" stroke-linecap="round"/></svg>
    <span>10:00 - 10:00</span>
  </div>
  <div class="abs phone">
    <svg width="18" height="30" viewBox="0 0 18 30"><rect x="1.5" y="1.5" width="15" height="27" rx="3" fill="none" stroke="#fff" stroke-width="2.4"/><circle cx="9" cy="24" r="1.6" fill="#fff"/></svg>
    <span>555 014 2290</span>
  </div>
</header>

<nav class="abs nav">
  <a class="active" style="left:78px">Home</a>
  <a style="left:156px">About Us</a>
  <a style="left:264px">Services</a>
  <a style="left:729px">Condition We Treat</a>
  <a style="left:912px">New Patient</a>
  <a style="left:1037px">Contact Us</a>
</nav>
<div class="abs brand">Maplecrest Behavioral Healthcare</div>

<section class="abs hero" role="img" aria-label="Photo of two people jumping joyfully against a bright sunset sky">
  <h1 class="abs">A step forward in your wellness journey.</h1>
  <a class="btn" style="left:78px;top:344px;width:230px">CONTACT NOW</a>
  <a class="btn" style="left:317px;top:344px;width:231px">MAKE APPOINTMENT</a>
</section>

<section class="abs about">
  <h2 class="section-title"><span>About <span class="hl">Maplecrest Behavioral Healthcare</span></span></h2>
  <p>Lorem Ipsum is simply dummy text of the printing and typesetting industry. Lorem Ipsum has been the industry's standard dummy text ever since the 1500s, when an unknown printer took a galley of type and scrambled it to make a type specimen book. It has survived not only five centuries, but also the leap into electronic typesetting, remaining essentially unchanged.</p>
</section>

<section class="abs mv">
  <div class="abs col" style="left:124px">
    <h2>Mission</h2>
    <p>To be the leading provider of outpatient psychiatric care in Atlanta Metro South, working together to promote (the) mental wellness of our community</p>
    <span class="pill">READ MORE</span>
  </div>
  <div class="abs col" style="left:696px">
    <h2>Vision</h2>
    <p>To provide mental health services to children, adults, and the developmentally disabled population that is culturally sensitive regardless of age, race..</p>
    <span class="pill">READ MORE</span>
  </div>
</section>

<section class="abs services">
  <h2 class="section-title"><span>Services <span class="hl">We Provide</span></span></h2>
</section>
<div class="abs ring"></div>
<div class="abs brain" role="img" aria-label="Colourful watercolour illustration of a brain"></div>

<div class="abs svc left" style="left:88px;top:1484px">Disability and<br>work-related reports</div>
<div class="abs icon" style="left:401px;top:1468px" role="img" aria-label="Icon of report documents"></div>
<div class="abs svc left" style="left:14px;top:1608px">Diagnostic evaluation<br>and treatment</div>
<div class="abs icon" style="left:332px;top:1585px" role="img" aria-label="Icon of a computer screen"></div>
<div class="abs svc left" style="left:24px;top:1738px">Psychopharmacology</div>
<div class="abs icon" style="left:360px;top:1710px" role="img" aria-label="Icon of medication organiser"></div>
<div class="abs svc left" style="left:106px;top:1842px">Bariatric pre-surgical<br>consultation</div>
<div class="abs icon" style="left:428px;top:1810px" role="img" aria-label="Icon of a consultation meeting"></div>

<div class="abs icon" style="left:712px;top:1468px" role="img" aria-label="Icon of a checklist clipboard"></div>
<div class="abs svc" style="left:812px;top:1480px">Early childhood<br>Assessments</div>
<div class="abs icon" style="left:772px;top:1570px" role="img" aria-label="Icon of a prohibition sign"></div>
<div class="abs svc" style="left:874px;top:1588px">Substance abuse<br>assessments</div>
<div class="abs icon" style="left:768px;top:1704px" role="img" aria-label="Icon of accessibility symbols"></div>
<div class="abs svc" style="left:874px;top:1732px">Developmental<br>disabilities</div>
<div class="abs icon" style="left:682px;top:1808px" role="img" aria-label="Icon of a wellness figure"></div>
<div class="abs svc" style="left:788px;top:1836px">Many more Prospective<br>Services</div>

<section class="abs conditions">
  <h2 class="section-title">Condition We Treat</h2>
  <div class="vline" style="left:422px;top:98px;height:150px"></div>
  <div class="vline" style="left:422px;top:310px;height:150px"></div>
  <div class="vline" style="left:776px;top:310px;height:150px"></div>
  <div class="hline" style="left:78px;top:279px;width:1044px"></div>

  <div class="cell" style="left:106px;top:138px;width:290px"><h3>Mood Disorders</h3><p>Depression, Bipolar, Seasonal Affective Disorder, Cyclothymic Disorder</p></div>
  <div class="cell" style="left:458px;top:142px;width:290px"><h3>Anxiety Disorders</h3><p>Generalized Anxiety, Panic, PTSD, OCD</p></div>
  <div class="cell boxed" style="left:776px;top:98px;width:346px;height:176px"><h3>Common Disorders of Childhood</h3><p>ADHD, Oppositional Defiant Disorder</p></div>

  <div class="cell" style="left:106px;top:346px;width:290px"><h3>Sleep Issues</h3><p>Depression, Bipolar, Seasonal Affective Disorder, Cyclothymic Disorder</p></div>
  <div class="cell" style="left:468px;top:356px;width:290px"><h3>Psychotic Disorders</h3><p>Schizophrenia, Brief Psychotic Episodes</p></div>
  <div class="cell" style="left:810px;top:356px;width:290px"><h3>And More</h3><p>Addiction, Eating Disorders</p></div>
</section>

<section class="abs news">
  <h2 class="section-title"><span>Latest <span class="hl">News</span></span></h2>
  <article class="post" style="top:65px">
    <div class="thumb" role="img" aria-label="Photo of a patient talking with a counsellor" style="background:linear-gradient(135deg,#dbe4ea,#9fb3c2)"></div>
    <div class="body">
      <div class="ttl">There are many variations of passages.</div>
      <div class="date"><svg width="13" height="13" viewBox="0 0 13 13"><rect x="1" y="2" width="11" height="10" fill="none" stroke="#2a90d6" stroke-width="1.5"/><path d="M1 5h11" stroke="#2a90d6" stroke-width="1.5"/></svg>8 July, 2017</div>
      <div>Lorem ipsum dolor sit amet, consectetur adipiscing elit.</div>
      <div class="more">READ MORE »</div>
    </div>
  </article>
  <div class="sep" style="top:190px"></div>
  <article class="post" style="top:226px">
    <div class="thumb" role="img" aria-label="Photo of a counsellor comforting a patient" style="background:linear-gradient(135deg,#efe7dc,#c9b7a2)"></div>
    <div class="body">
      <div class="ttl">There are many variations of passages.</div>
      <div class="date"><svg width="13" height="13" viewBox="0 0 13 13"><rect x="1" y="2" width="11" height="10" fill="none" stroke="#2a90d6" stroke-width="1.5"/><path d="M1 5h11" stroke="#2a90d6" stroke-width="1.5"/></svg>8 July, 2017</div>
      <div>Lorem ipsum dolor sit amet, consectetur adipiscing elit.</div>
      <div class="more">READ MORE »</div>
    </div>
  </article>
</section>

<section class="abs faq">
  <h2 class="section-title">FAQ</h2>
  <div class="faq-list">
    <div class="faq-item"><span class="sign">−</span>What do I need to bring with me to my first visit?</div>
    <div class="faq-answer">Insurance card, patient forms found on our</div>
    <div class="faq-item"><span class="sign">+</span>How long do I have to wait to be seen?</div>
    <div class="faq-item"><span class="sign">+</span>What typs of insurance do you accept?</div>
    <div class="faq-item"><span class="sign">+</span>Why is my child not doing well in school?</div>
    <div class="faq-item"><span class="sign">+</span>What if my care givers cancel?</div>
  </div>
</section>

<section class="abs packet">New Patient Packet Click To <a>Download</a></section>

<footer class="abs footer">
  <div class="col" style="left:78px">
    <h4>Links</h4>
    <div class="links">
      <span>Home</span><span>Payment Policy</span>
      <span>About Us</span><span>Bio, Philosophy</span>
      <span>Cancellation Policy</span><span>Event Calender</span>
      <span>Call Policy</span><span>News &amp; Community</span>
      <span>FAQ</span>
    </div>
  </div>
  <div class="col" style="left:436px;width:320px">
    <h4>Recent tweets</h4>
    <div class="tweet"><span class="dot"></span><div>@lenaharlow @brightpathstudio<br>Thank you very much.<br>4 days ago</div></div>
    <div class="tweet"><span class="dot"></span><div>@lenaharlow @brightpathstudio<br>Thank you very much.<br>4 days ago</div></div>
  </div>
  <div class="col" style="left:791px;width:330px">
    <h4>Contact Info</h4>
    <div class="contact-row"><svg width="16" height="22" viewBox="0 0 16 22"><path d="M8 1a7 7 0 0 0-7 7c0 5 7 13 7 13s7-8 7-13a7 7 0 0 0-7-7z" fill="#fff"/><circle cx="8" cy="8" r="2.6" fill="#1f7fc4"/></svg><span>48 Redbud Lane, Fayetteville, GA<br>United States</span></div>
    <div class="contact-row"><svg width="18" height="18" viewBox="0 0 18 18"><path d="M4 1l3 4-2 2c1 2 3 4 5 5l2-2 4 3-2 3C8 16 2 10 1 4z" fill="#fff"/></svg><span>555 014 2290</span></div>
    <div class="contact-row"><svg width="18" height="14" viewBox="0 0 18 14"><rect x="1" y="1" width="16" height="12" fill="none" stroke="#fff" stroke-width="1.6"/><path d="M1 1l8 7 8-7" fill="none" stroke="#fff" stroke-width="1.6"/></svg><span>hello@maplecrestbh.com</span></div>
  </div>
</footer>

<div class="abs totop"><svg width="60" height="36" viewBox="0 0 60 36"><path d="M22 22l8-8 8 8" fill="none" stroke="#fff" stroke-width="3"/></svg></div>

<div class="abs bottombar">
  <div class="abs copy">©Maplecrest behavioral healthcare. 2017 - All Rights Reserved.</div>
  <span class="abs social" style="left:1004px"></span>
  <span class="abs social" style="left:1050px"></span>
  <span class="abs social" style="left:1096px"></span>
</div>

</body>
</html>
```